Business Card Design for Occupational Medicine Start Up Company

We need to design a professional business card. We are a healthcare company providing occupational medicine services to blue collar industries. We are professional, efficient and high quality service providers.

Target Market(s)

Blue Collar Industry: Shipbuilding, Ports, Trucking Companies; The Executives and Safety Officers for these companies

Industry/Entity Type

Healthcare

Contact Information for Business Card

Logo, Name, Title, Email, Phone

Other font styles liked:
• Please match our Brand Guide

Requirements
Must have
• Our Company Colors and Logo

```html
<!DOCTYPE html>
<html lang="en">
<head>
<meta charset="utf-8">
<title>Harborline Clinics – Business Card</title>
<link href="https://fonts.googleapis.com/css2?family=Montserrat:wght@400;500;700;800&family=Arimo:wght@400&display=swap" rel="stylesheet">
<style>
  :root{
    --navy:#27338a;
    --sky:#3aa6dd;
    --amber:#f0a535;
    --ink:#111111;
    --paper:#ffffff;
    --card-black:#161616;
    --emboss:#262626;
    --stage:#d9d9dc;
    --rule:#9a9a9a;
  }
  html,body{margin:0;padding:0;overflow:hidden;}
  body{
    width:1200px;height:1040px;background:var(--stage);
    display:flex;flex-direction:column;align-items:center;justify-content:center;gap:50px;
    font-family:"Montserrat",sans-serif;
  }
  .card{
    width:720px;height:410px;position:relative;box-sizing:border-box;
    border-radius:0 70px 0 70px;
    box-shadow:0 10px 30px rgba(0,0,0,.25);
  }
  .card--back{background:var(--card-black);display:flex;align-items:center;justify-content:center;}
  .back-mark{display:flex;align-items:center;gap:16px;color:var(--emboss);
    font-weight:800;font-size:40px;letter-spacing:1px;text-transform:uppercase;}
  .back-mark .dot{width:40px;height:40px;border-radius:50%;background:var(--emboss);}
  .card--front{background:var(--paper);display:flex;align-items:center;}
  .brand{width:355px;display:flex;flex-direction:column;align-items:center;gap:16px;}
  .brand .dot{width:60px;height:60px;border-radius:50%;background:var(--sky);}
  .brand .name{color:var(--navy);font-weight:700;font-size:31px;letter-spacing:1px;text-transform:uppercase;text-align:center;line-height:1.15;}
  .divider{width:1px;height:250px;background:var(--rule);}
  .contact{padding-left:40px;color:var(--ink);font-family:"Arimo",sans-serif;font-size:19px;}
  .person{font-family:"Montserrat",sans-serif;color:var(--navy);font-size:27px;text-transform:uppercase;letter-spacing:1px;margin:0;}
  .person b{font-weight:800;}
  .person span{font-weight:400;}
  .role{margin:2px 0 16px;font-size:19px;}
  .line{display:flex;align-items:center;gap:10px;margin:4px 0;}
  .line svg{width:18px;height:18px;fill:none;stroke:var(--navy);stroke-width:2;}
  .web em{font-style:normal;color:var(--navy);}
  .address{margin-top:14px;line-height:1.3;}
</style>
</head>
<body>
  <section class="card card--back">
    <div class="back-mark"><span class="dot"></span>Harborline</div>
  </section>

  <section class="card card--front">
    <div class="brand">
      <span class="dot"></span>
      <div class="name">Harborline<br>Clinics</div>
    </div>
    <div class="divider"></div>
    <div class="contact">
      <p class="person"><b>Daniel</b> <span>Reyes</span></p>
      <p class="role">Managing Director</p>
      <div class="line">
        <svg viewBox="0 0 24 24"><path d="M5 3h4l2 5-2.5 1.5a11 11 0 0 0 6 6L16 13l5 2v4a2 2 0 0 1-2 2A16 16 0 0 1 3 5a2 2 0 0 1 2-2z"/></svg>
        044-987 654 321
      </div>
      <div class="line">
        <svg viewBox="0 0 24 24"><rect x="3" y="5" width="18" height="14"/><path d="M3 5l9 8 9-8"/></svg>
        hello@harborline.com
      </div>
      <div class="line web">
        <svg viewBox="0 0 24 24"><circle cx="12" cy="12" r="9"/><path d="M3 12h18M12 3c3 3 3 15 0 18M12 3c-3 3-3 15 0 18"/></svg>
        <span>www.<em>harborline</em>.com</span>
      </div>
      <div class="address">421, Address line goes here<br>45452,Country Name</div>
    </div>
  </section>
</body>
</html>
```